KLV Plant Services

We are a heavy diesel mechanical business with additional air con certificates, remapping engine rebuilt

Contact Information for Business Card

Company Name, Director Name, Managing Director, Contact details, email and website

Font styles to use
Serif
Script

```html
<!DOCTYPE html>
<html lang="en">
<head>
<meta charset="utf-8">
<title>KLV Plant Services – Business Cards</title>
<link href="https://fonts.googleapis.com/css2?family=Ubuntu:wght@400;500;700&display=swap" rel="stylesheet">
<style>
  :root {
    --bg: #2b2d31;
    --navy: #25227a;
    --navy-deep: #1c1a63;
    --white: #ffffff;
    --muted: #d9d8f0;
    --art-light: #f2f2f2;
    --art-dark: #cfcfd4;
  }
  * { margin: 0; padding: 0; box-sizing: border-box; }
  html, body {
    width: 1200px; height: 900px; overflow: hidden;
    background: var(--bg);
    font-family: "Ubuntu", sans-serif;
  }
  .stage { position: relative; width: 1200px; height: 900px; }

  .card {
    position: absolute;
    border-radius: 22px;
    overflow: hidden;
    background: linear-gradient(160deg, var(--navy) 0%, var(--navy-deep) 100%);
    box-shadow: 0 18px 40px rgba(0,0,0,.45);
  }

  /* Front: vertical contact card */
  .card-front { left: 110px; top: 150px; width: 340px; height: 595px; }
  .front-brand {
    position: absolute; left: 34px; top: 40px;
    display: flex; align-items: center; gap: 10px;
    color: var(--white); font-weight: 700; font-size: 22px; letter-spacing: .3px;
    white-space: nowrap;
  }
  .brand-dot {
    width: 14px; height: 14px; border-radius: 50%;
    background: var(--white); flex: none;
  }
  .contact { position: absolute; left: 34px; top: 104px; right: 20px; color: var(--white); }
  .contact .name { font-weight: 700; font-size: 19px; letter-spacing: .5px; }
  .contact .role { font-size: 13px; color: var(--muted); margin-top: 3px; }
  .contact .address { font-size: 13px; color: var(--muted); margin-top: 16px; line-height: 1.45; }
  .contact ul { list-style: none; margin-top: 14px; }
  .contact li {
    display: flex; align-items: center; gap: 9px;
    font-size: 13px; line-height: 1.9; white-space: nowrap;
  }
  .contact li svg { width: 12px; height: 12px; fill: var(--white); flex: none; }
  .front-art { position: absolute; left: 0; bottom: 0; width: 340px; height: 280px; }

  /* Back: horizontal brand card */
  .card-back { left: 520px; top: 275px; width: 595px; height: 340px; }
  .back-brand {
    position: absolute; inset: 0;
    display: flex; align-items: center; justify-content: center; gap: 16px;
    color: var(--white); font-weight: 700; font-size: 40px; letter-spacing: .5px;
    white-space: nowrap;
  }
  .back-brand .brand-dot { width: 24px; height: 24px; }
</style>
</head>
<body>
<main class="stage">

  <section class="card card-front" aria-label="Business card front">
    <div class="front-brand"><span class="brand-dot"></span>KLV Plant Services</div>
    <div class="contact">
      <p class="name">DANIEL HARWOOD</p>
      <p class="role">Managing Director</p>
      <p class="address">P.O. Box 48, Mill Road<br>Riverton ON, K2L 4M8</p>
      <ul>
        <li>
          <svg viewBox="0 0 24 24"><path d="M6.6 10.8a15.1 15.1 0 0 0 6.6 6.6l2.2-2.2c.3-.3.7-.4 1-.2 1.1.4 2.3.6 3.6.6.6 0 1 .4 1 1V20c0 .6-.4 1-1 1A17 17 0 0 1 3 4c0-.6.4-1 1-1h3.5c.6 0 1 .4 1 1 0 1.3.2 2.5.6 3.6.1.3 0 .7-.2 1z"/></svg>
          555-214-7390
        </li>
        <li>
          <svg viewBox="0 0 24 24"><path d="M2 5h20v14H2z M2 5l10 8 10-8" fill="none" stroke="#fff" stroke-width="2"/></svg>
          info@klvplantservices.com
        </li>
        <li>
          <svg viewBox="0 0 24 24"><circle cx="12" cy="12" r="9" fill="none" stroke="#fff" stroke-width="2"/><path d="M3 12h18M12 3c3 3 3 15 0 18M12 3c-3 3-3 15 0 18" fill="none" stroke="#fff" stroke-width="1.6"/></svg>
          www.klvplantservices.com
        </li>
      </ul>
    </div>
    <svg class="front-art" viewBox="0 0 340 280" role="img" aria-label="Excavator arm and bucket silhouette">
      <defs>
        <linearGradient id="artFill" x1="0" y1="0" x2="1" y2="1">
          <stop offset="0" stop-color="#cfcfd4"/>
          <stop offset=".45" stop-color="#f2f2f2"/>
          <stop offset="1" stop-color="#ffffff"/>
        </linearGradient>
      </defs>
      <path d="M0 190 C40 150 70 90 110 70 L300 0 C320 -4 340 10 340 30 L340 280 L0 280 Z" fill="url(#artFill)"/>
    </svg>
  </section>

  <section class="card card-back" aria-label="Business card back">
    <div class="back-brand"><span class="brand-dot"></span>KLV Plant Services</div>
  </section>

</main>
</body>
</html>
```